Vibrant, yet professional, stationery set and other designs required.

I need to source a fantastic designer for a new project as part of my company using a new logo designed via sketch harbor.

**UPDATE** I am not looking for just 'fine' design that will suffice. I am looking for something great.

We are a life assurance brokerage based in Dublin, Ireland and BrightRoost.ie is our new website aimed at providing services for young families in Ireland. We are hoping to be the 'Velro' level of service providers in this area and I am looking for the quality of design to reflect this :-) Hopefully that makes sense!

I have a preference for straight lines over curves and waves.

I need...

1. Business card
2. Letterhead
3. Banner (for printing - 76cm X 305cm)
4. Car branding for KORVA 9 (2014 sport model) I believe the templates are freely available online.

Target Market(s)

Parents in Ireland - Aged 27 to 50.

Industry/Entity Type

Financial Planning

Colors

Designer to choose colors to be used in the design.

Requirements
Must have
• All of the items listed in the description above. I like clean, bright, legible, vibrant and professional design.
Should not have
• No silly or 'cheap' looking designs. This is a professional company looking to provide a professional service.

```html
<!DOCTYPE html>
<html lang="en">
<head>
<meta charset="utf-8">
<title>BrightRoost.ie Business Card</title>
<link rel="stylesheet" href="https://fonts.googleapis.com/css2?family=Roboto:wght@400;500&display=swap">
<style>
  :root {
    --page: #d9d4cf;
    --card: #eeedeb;
    --ink: #4f5962;
    --ink-soft: #5d6770;
    --orange: #e2531f;
    --green: #6aad2c;
    --teal: #1f7f8e;
  }
  html, body {
    margin: 0;
    width: 1200px;
    height: 969px;
    overflow: hidden;
    background: var(--page);
    font-family: "Roboto", Arial, sans-serif;
  }
  .card {
    position: absolute;
    left: 100px;
    top: 200px;
    width: 1000px;
    height: 570px;
    background: var(--card);
    box-shadow: 0 2px 10px rgba(0,0,0,0.12);
    overflow: hidden;
  }
  .brand {
    position: absolute;
    left: 55px;
    top: 52px;
    margin: 0;
    font-size: 60px;
    font-weight: 500;
    line-height: 1;
    color: var(--ink);
    letter-spacing: -0.5px;
  }
  .accent-bar {
    position: absolute;
    left: 0;
    top: 229px;
    width: 14px;
    height: 72px;
    background: var(--green);
  }
  .holder-name {
    position: absolute;
    left: 55px;
    top: 230px;
    margin: 0;
    font-size: 31px;
    font-weight: 500;
    color: var(--orange);
    text-transform: uppercase;
  }
  .holder-role {
    position: absolute;
    left: 55px;
    top: 272px;
    margin: 0;
    font-size: 24px;
    color: var(--ink-soft);
    text-transform: uppercase;
  }
  .address {
    position: absolute;
    left: 55px;
    top: 322px;
    margin: 0;
    font-size: 24px;
    line-height: 31px;
    font-style: normal;
    color: var(--ink);
  }
  .contacts {
    position: absolute;
    left: 55px;
    top: 390px;
    margin: 0;
    padding: 0;
    list-style: none;
    font-size: 24px;
    line-height: 32.5px;
    color: var(--ink);
  }
  .contacts li {
    display: flex;
    align-items: center;
    gap: 14px;
  }
  .contacts svg {
    width: 20px;
    height: 20px;
    fill: var(--orange);
    flex: none;
  }
  .family-art {
    position: absolute;
    left: 537px;
    top: 22px;
    width: 400px;
    height: 548px;
    background: linear-gradient(90deg, rgba(31,127,142,0.75) 0%, rgba(226,83,31,0.75) 50%, rgba(106,173,44,0.8) 100%);
  }
</style>
</head>
<body>
  <main class="card">
    <h1 class="brand">BrightRoost.ie</h1>
    <div class="accent-bar"></div>
    <p class="holder-name">Niamh Keller</p>
    <p class="holder-role">CEO/Founder</p>
    <address class="address">214 Harlow Quay<br>Dunmore, Leinster 40218</address>
    <ul class="contacts">
      <li>
        <svg viewBox="0 0 20 20" aria-hidden="true"><path d="M4 1l4 4-2 3c1.5 3 3 4.5 6 6l3-2 4 4-3 3C8 18 2 12 1 4z"/></svg>
        671 204 3385
      </li>
      <li>
        <svg viewBox="0 0 20 20" aria-hidden="true"><path d="M5 0h10a1 1 0 011 1v18a1 1 0 01-1 1H5a1 1 0 01-1-1V1a1 1 0 011-1zm1 3v12h8V3zm4 13a1.2 1.2 0 100 2.4A1.2 1.2 0 0010 16z"/></svg>
        852 713 4096
      </li>
      <li>
        <svg viewBox="0 0 20 20" aria-hidden="true"><path d="M5 1h10v5H5zM1 7h18v8h-3v-3H4v3H1zm4 6h10v6H5z"/></svg>
        495 318 2067
      </li>
      <li>
        <svg viewBox="0 0 20 20" aria-hidden="true"><path d="M1 4h18v12H1zm1.5 1.5L10 11l7.5-5.5V6L10 12 2.5 6z"/></svg>
        hello@brightroost.ie
      </li>
      <li>
        <svg viewBox="0 0 20 20" aria-hidden="true"><circle cx="10" cy="10" r="9"/></svg>
        www.brightroost.ie
      </li>
    </ul>
    <div class="family-art" role="img" aria-label="Illustration of three stylised family figures in teal, orange and green"></div>
  </main>
</body>
</html>
```